Church Website with Home Page and Member Sermon Library

I am in need of an updated design for our church website. This will include 4 pages (outlined below). We are a conservative, evangelical, Christian church. The site should be modern and clean, while still reflecting our conservative values. I already have a logo for our church, and I want the site to incorporate the logo, and match the logo/branding. Stock photos are allowed if needed, but I have uploaded some images of our church and would prefer those images to be used if possible. Any stock photos used should not include any people in the photos (scenery, nature, buildings, animals, etc. are fine).

The site will need 4 pages: Home, Support Us (Donate), Login, and Recording Library.

Page 1: Home
The home page should include the following sections:

- Navigation: Should include links to each section of the home page plus a "listen live" link which will take the user to a live-streaming site and a "support us" link which will take the user to a support/donate page.

- Announcements: Can be either a banner or some other design, but there needs to be some way for us to post announcements for visitors to see. I'm open for creative ideas in this section, but would like it not to take up a lot of room on the page.

- About Us: Should include address, service times (see attached document), and information about the church.

- Pastor Bio: A section that introduces our pastor and gives a short bio about our pastor. Would like this section to include a picture of our pastor. Somewhere in this section I would like to include this Bible reference: "And I will give you pastors according to mine heart, which shall feed you with knowledge and understanding. Jer 3:15 LPW"

- Articles of Faith (What We Believe): This should include several sub-sections each with a heading, body, and possibly 1 or more scripture references. I have attached a document to the brief that includes our articles of faith. Feel free to be creative with this section in how you lay these out and format them.

- Support Us: A small section that explains what kind of support someone can give and a link to a donation page. The link can say something like "Support Us" or "Donate Now".

- Contact form: A contact form that allows the visitor to send us a message. The contact form should ask for name, email, phone, and message.

- Footer: A footer that will be displayed on all pages of the site. This should include at a minimum a link to the home page (or a link to each individual section in the home page if you prefer), a link to "listen live", a link to "support us", a link to "contact us" (or you can put the contact form directly in the footer if you prefer), the address, and a "member login" link.

Page 2: Support Us
The donation page should include a form the visitor can fill out to make a donation. We will embed a third party form later. For this design, please just mock out the design with a basic form asking for name, phone, and email.

Page 3: Login
The recording library (detailed below) will require members to login with a shared numeric code before accessing the page. We need a design for a login screen. The screen should include navigation/footer just like all other pages, but the body of the login page will consist only of a form that asks the user to enter the access code and then a "login" button.

Page 4: Recording Library

The library page is a member-only page that will require a shared, numeric pass code to access. On this page, members will be able to access a filterable list of past sermons. The page by default should display most recent sermons, but should also include a search form that allows the member to filter the sermon list to find a particular sermon. The search form should allow the user to select a filter type (e.g. Speaker name, date, event, etc.) and type in a value to search. They should be able to add multiple filters and remove filters that have been added. Each sermon that is displayed in the result list should include basic information such as title, date, speaker, tags, etc. along with a download icon, and an embedded audio player where they can click a play button to stream it on-demand. Each sermon should also have clickable tags associated with it that can be used to find related sermons.
Updates

I have uploaded several images of our church. Feel free to incorporate these into your design if possible.

Target Market(s)

Church Members

Industry/Entity Type

Religion

Number of Pages Required

4 page

Font styles to use
Sans Serif

Colors

Designer to choose colors to be used in the design.

Requirements
Must have
• Must incorporate the logo (attached)
Nice to have
• Would like the design to incorporate pictures of our church (attached) instead of stock photos if possible.
Should not have
• Please avoid an overly cluttered design. Stock photos used should not include any people in the photos.

```html
<!DOCTYPE html>
<html lang="en">
<head>
<meta charset="utf-8">
<title>Grace Hill Church</title>
<link href="https://fonts.googleapis.com/css2?family=Raleway:wght@400;500;600;700&family=Montserrat:wght@400;500;600;700&display=swap" rel="stylesheet">
<style>
:root{
  --dark:#222222;
  --dark-2:#2a2a2a;
  --card:#3a3a3a;
  --gold:#d4a24c;
  --gold-deep:#c99a3f;
  --white:#ffffff;
  --muted:#bdbdbd;
  --paper:#ececec;
  --sky:#f2f7fa;
  --green:#5e8a48;
  --cyan:#00bcd6;
  --ink:#1c1c1c;
  --footer:#272727;
}
*{margin:0;padding:0;box-sizing:border-box}
html,body{width:1200px;height:5029px;overflow:hidden}
body{position:relative;background:var(--dark);font-family:"Montserrat",sans-serif;color:var(--white)}
.abs{position:absolute}
.heading{font-family:"Raleway",sans-serif;font-weight:400}
.btn{position:absolute;display:flex;align-items:center;justify-content:center;gap:14px;font-size:13px;font-family:"Montserrat",sans-serif;color:var(--white);text-decoration:none;background:var(--ink);border:1px solid transparent}
.btn.outline-gold{background:transparent;border-color:var(--gold)}
.btn svg{width:8px;height:12px}
.brand{display:flex;align-items:center;gap:8px;font-family:"Raleway",sans-serif;font-weight:500;letter-spacing:2px;color:var(--white);font-size:17px}
.brand .mark{width:10px;height:10px;border:1.5px solid var(--white)}

/* hero */
.hero{left:0;top:0;width:1200px;height:624px;background:linear-gradient(180deg,#6f6a66 0%,#7d6f62 45%,#5a5652 75%,#3e3d3d 100%)}
.hero-shade{left:0;top:0;width:1200px;height:624px;background:rgba(30,30,30,.45)}
.nav a{position:absolute;top:50px;font-size:12px;color:var(--white);text-decoration:none}
.hero-title{left:0;width:1200px;top:202px;text-align:center;font-size:56px;line-height:72px;color:var(--white)}
.hero-foot{top:568px;font-size:12px}

/* service */
.service-photo{left:131px;top:728px;width:407px;height:480px;background:linear-gradient(180deg,#dcdcdc 0%,#cfcfcf 45%,#8a6f5a 55%,#b9ada0 70%,#d2cabf 100%)}
.service-frame{left:146px;top:742px;width:377px;height:452px;border:2px solid var(--gold);border-radius:14px}
.slider{top:1221px;font-size:8px;color:#aaa}
.slider-line{left:253px;top:1226px;width:250px;height:1px;background:#666}
.slider-line i{position:absolute;left:0;top:-1px;width:150px;height:3px;background:#ddd}
.service-title{left:593px;top:742px;font-size:38px;line-height:50px}
.body-small{font-size:9.5px;line-height:17px;color:#cfcfcf}
.time-box{position:absolute;width:222px;height:80px;background:var(--card);border-radius:3px;padding:14px 12px}
.time-box .lbl{display:flex;align-items:center;gap:8px;font-size:13px;color:var(--gold)}
.time-box .val{margin-top:14px;font-size:17px;color:var(--white);font-weight:500}

/* pastor */
.pastor-title{left:195px;top:1428px;font-size:36px;line-height:50px}
.pastor-photo{left:722px;top:1327px;width:256px;height:420px;background:linear-gradient(180deg,#4a4a4a 0%,#2b2b2b 40%,#1f1f1f 70%,#6b5a3c 100%);border-radius:60px 60px 0 0}
.pastor-frame{left:695px;top:1418px;width:310px;height:342px;border:9px solid var(--gold-deep)}
.pastor-tag{left:735px;top:1722px;width:170px;height:26px;background:var(--gold-deep);color:var(--ink);font-size:12px;display:flex;align-items:center;padding-left:8px;gap:5px}
.pastor-tag i{width:7px;height:7px;border-radius:50%;background:var(--ink);display:block}

/* sermons */
.sermons{left:0;top:1854px;width:1200px;height:843px;background:var(--paper)}
.section-title{position:absolute;left:0;width:1200px;text-align:center;font-family:"Raleway",sans-serif;font-size:37px;line-height:50px;color:var(--ink)}
.sermon-card{position:absolute;width:191px;height:225px;background:var(--dark-2);border-radius:3px;text-align:center}
.sermon-card .avatar{width:28px;height:28px;border-radius:50%;margin:22px auto 0;background:linear-gradient(135deg,#b07a4e,#5c5c5c)}
.sermon-card .by{font-size:9px;margin-top:8px;color:var(--white)}
.sermon-card h3{font-family:"Montserrat",sans-serif;font-weight:500;font-size:14.5px;line-height:19px;margin:14px 14px 0}
.sermon-card .tag{display:inline-block;margin-top:8px;background:var(--white);color:#c0662a;font-size:7px;padding:3px 10px;border-bottom:2px solid var(--gold)}
.player{position:absolute;left:10px;right:10px;bottom:12px;display:flex;align-items:center;gap:8px}
.player .play{width:22px;height:22px;border-radius:50%;background:var(--white);display:flex;align-items:center;justify-content:center}
.player .bar{flex:1;height:2px;background:#777;position:relative}
.player .bar i{position:absolute;left:0;top:0;width:30%;height:2px;background:var(--gold)}
.player .time{font-size:7px;color:#ccc}

/* articles */
.articles{left:0;top:2697px;width:1200px;height:643px;background:var(--sky)}
.article{position:absolute;top:2841px;width:260px;color:var(--ink)}
.article .pic{height:236px;border-radius:6px}
.article .kicker{margin:22px 0 0 10px;font-size:9px;font-weight:600}
.article h3{margin:6px 0 0 10px;font-size:17px;font-weight:600}
.article p{margin:14px 10px 0 10px;font-size:9.5px;line-height:17px;color:#444}
.article .more{margin:18px 0 0 10px;font-size:9px;font-weight:600;display:flex;align-items:center;gap:6px}

/* support */
.support{left:0;top:3340px;width:1200px;height:305px;background:var(--green);text-align:center}
.support h2{position:absolute;left:0;width:1200px;top:62px;font-family:"Raleway",sans-serif;font-weight:700;font-size:29px}
.support p{position:absolute;left:250px;width:700px;top:126px;font-size:11px;line-height:20px;color:#eef3ea}

/* announcements */
.light-title{position:absolute;left:0;width:1200px;text-align:center;font-family:"Raleway",sans-serif;font-size:37px;color:var(--white)}
.notice-left{left:195px;top:3812px;width:408px;height:211px;background:var(--gold-deep)}
.notice-art{left:205px;top:3830px;width:185px;height:172px;background:linear-gradient(135deg,#e6b968,#b98a33);border-radius:6px}
.notice-left h3{position:absolute;right:12px;top:28px;text-align:right;font-family:"Raleway",sans-serif;font-weight:700;font-size:30px;line-height:36px;color:var(--ink)}
.notice-left .when{position:absolute;right:12px;top:135px;text-align:right;font-size:13px;line-height:26px;color:var(--ink)}
.notice-right{left:618px;top:3812px;width:387px;height:211px;background:var(--white);color:var(--ink)}
.notice-right .brand{position:absolute;left:16px;top:28px;color:var(--ink);font-size:9px;letter-spacing:1px}
.notice-right .brand .mark{border-color:var(--ink);width:7px;height:7px}
.notice-right .head{position:absolute;right:20px;top:22px;font-size:14px}
.notice-right .art{position:absolute;left:110px;top:52px;width:260px;height:145px;background:linear-gradient(135deg,#f7c23c,#f07a1a 70%,#e8e8e8);border-radius:6px}

/* contact */
.contact{left:330px;top:4183px;width:540px;height:384px;background:var(--cyan)}
.field{position:absolute;width:200px;font-size:11px;color:var(--white)}
.field .line{margin-top:14px;border-bottom:1px solid rgba(255,255,255,.75);height:20px;display:flex;align-items:center;gap:7px;font-size:10px;color:rgba(255,255,255,.8)}

/* footer */
.footer{left:0;top:4655px;width:1200px;height:374px;background:var(--footer);text-align:center}
.footer-nav{position:absolute;left:0;width:1200px;top:180px;display:flex;justify-content:center;gap:30px;font-size:11px;color:#ddd}
.footer .addr{position:absolute;left:0;width:1200px;top:223px;font-size:11px;color:#ddd}
.socials{position:absolute;left:0;width:1200px;top:257px;display:flex;justify-content:center;gap:14px}
.socials span{width:32px;height:32px;border-radius:50%;background:var(--cyan);display:block}
.footer .copy{position:absolute;left:0;width:1200px;top:306px;font-size:11px;color:#ddd}
</style>
</head>
<body>

<!-- Hero -->
<section>
  <div class="abs hero" role="img" aria-label="Photograph of the brick church building and parking lot"></div>
  <div class="abs hero-shade"></div>
  <nav class="nav">
    <a style="left:194px">Home</a>
    <a style="left:263px">About</a>
    <a style="left:334px">Pastor</a>
    <a style="left:404px">Listen Live</a>
    <a style="left:751px">Library</a>
    <a style="left:826px">Donation</a>
    <a style="left:912px">Support Us</a>
    <a style="left:1010px">Contact</a>
  </nav>
  <div class="abs brand" style="left:526px;top:46px"><span class="mark"></span>GRACE HILL</div>
  <h1 class="abs heading hero-title">I am the way, and the<br>truth and the life.</h1>
  <a class="btn" style="left:532px;top:390px;width:136px;height:40px">Book A visit <svg viewBox="0 0 8 12"><path d="M1 1l5 5-5 5" fill="none" stroke="#fff" stroke-width="1.5"/></svg></a>
  <div class="abs hero-foot" style="left:194px">Stream Sermons</div>
  <div class="abs hero-foot" style="left:857px">Community</div>
  <div class="abs hero-foot" style="left:950px">Gallery</div>
</section>

<!-- Service times -->
<section>
  <div class="abs service-photo" role="img" aria-label="Photograph of the church building across an open field"></div>
  <div class="abs service-frame"></div>
  <div class="abs slider" style="left:220px">PREV</div>
  <div class="abs slider-line"><i></i></div>
  <div class="abs slider" style="left:514px">NEXT</div>

  <h2 class="abs heading service-title">Grace Hill<br>Church Service Time</h2>
  <p class="abs body-small" style="left:593px;top:850px;width:420px">Join us each week as we gather to worship, pray and open the Word together. All are welcome, whether this is your first visit or you have been with us for years.</p>
  <p class="abs body-small" style="left:593px;top:907px;width:420px">Our doors open thirty minutes early, with coffee in the fellowship hall and a warm welcome at every entrance.</p>

  <div class="time-box" style="left:593px;top:973px"><div class="lbl"><svg width="13" height="13" viewBox="0 0 13 13"><rect x="1" y="2" width="11" height="10" rx="1" fill="none" stroke="#d4a24c"/><path d="M1 5h11M4 1v2M9 1v2" stroke="#d4a24c"/></svg>Wednesday Evening</div><div class="val">7:30 PM</div></div>
  <div class="time-box" style="left:827px;top:973px"><div class="lbl"><svg width="13" height="13" viewBox="0 0 13 13"><rect x="1" y="2" width="11" height="10" rx="1" fill="none" stroke="#d4a24c"/><path d="M1 5h11M4 1v2M9 1v2" stroke="#d4a24c"/></svg>Sunday School</div><div class="val">10:00 AM</div></div>
  <div class="time-box" style="left:593px;top:1069px"><div class="lbl"><svg width="13" height="13" viewBox="0 0 13 13"><rect x="1" y="2" width="11" height="10" rx="1" fill="none" stroke="#d4a24c"/><path d="M1 5h11M4 1v2M9 1v2" stroke="#d4a24c"/></svg>Sunday Morning</div><div class="val">11:00 AM</div></div>
  <div class="time-box" style="left:827px;top:1069px"><div class="lbl"><svg width="13" height="13" viewBox="0 0 13 13"><rect x="1" y="2" width="11" height="10" rx="1" fill="none" stroke="#d4a24c"/><path d="M1 5h11M4 1v2M9 1v2" stroke="#d4a24c"/></svg>Sunday Evening</div><div class="val">5:30 PM</div></div>

  <a class="btn outline-gold" style="left:593px;top:1182px;width:134px;height:40px">Book A visit <svg viewBox="0 0 8 12"><path d="M1 1l5 5-5 5" fill="none" stroke="#fff" stroke-width="1.5"/></svg></a>
</section>

<!-- Pastor -->
<section>
  <h2 class="abs heading pastor-title">Pastor of Grace Hill<br>Church</h2>
  <p class="abs body-small" style="left:195px;top:1542px;width:420px">Cornerstone Fellowship is a multi-campus church throughout the Lakeshore area. We offer live in-person services as well as livestreaming online-only options for our members who are unable to attend. If you are new, we are checking in with you for the first time, welcome.</p>
  <p class="abs body-small" style="left:195px;top:1622px;width:420px">Bible reference: "And I will give you pastors according to mine heart, which shall feed you with knowledge and understanding." Jer 3:15 LPW</p>
  <a class="btn outline-gold" style="left:195px;top:1686px;width:134px;height:40px">Know More <svg viewBox="0 0 8 12"><path d="M1 1l5 5-5 5" fill="none" stroke="#fff" stroke-width="1.5"/></svg></a>

  <div class="abs pastor-frame"></div>
  <div class="abs pastor-photo" role="img" aria-label="Portrait photograph of the pastor holding a Bible"></div>
  <div class="abs pastor-tag"><i></i>Pastor Elias Marsh</div>
</section>

<!-- Sermons -->
<section>
  <div class="abs sermons"></div>
  <h2 class="section-title" style="top:1932px">Sermon Recordings<br>/ Live-streaming</h2>

  <article class="sermon-card" style="left:195px;top:2072px"><div class="avatar" role="img" aria-label="Speaker portrait"></div><div class="by">Spoken By Ruth K.</div><h3>Printer took a galley of type and scrambled it to</h3><span class="tag">Sermon 1</span><div class="player"><span class="play"><svg width="7" height="8" viewBox="0 0 7 8"><path d="M0 0l7 4-7 4z" fill="#222"/></svg></span><span class="bar"><i></i></span><span class="time">00:00</span></div></article>
  <article class="sermon-card" style="left:400px;top:2072px"><div class="avatar" role="img" aria-label="Speaker portrait"></div><div class="by">Spoken By Ruth K.</div><h3>Printer took a galley of type and scrambled it to</h3><span class="tag">Sermon 2</span><div class="player"><span class="play"><svg width="7" height="8" viewBox="0 0 7 8"><path d="M0 0l7 4-7 4z" fill="#222"/></svg></span><span class="bar"><i></i></span><span class="time">00:00</span></div></article>
  <article class="sermon-card" style="left:607px;top:2072px"><div class="avatar" role="img" aria-label="Speaker portrait"></div><div class="by">Spoken By Ruth K.</div><h3>Printer took a galley of type and scrambled it to</h3><span class="tag">Sermon 3</span><div class="player"><span class="play"><svg width="7" height="8" viewBox="0 0 7 8"><path d="M0 0l7 4-7 4z" fill="#222"/></svg></span><span class="bar"><i></i></span><span class="time">00:00</span></div></article>
  <article class="sermon-card" style="left:814px;top:2072px"><div class="avatar" role="img" aria-label="Speaker portrait"></div><div class="by">Spoken By Ruth K.</div><h3>Printer took a galley of type and scrambled it to</h3><span class="tag">Sermon 4</span><div class="player"><span class="play"><svg width="7" height="8" viewBox="0 0 7 8"><path d="M0 0l7 4-7 4z" fill="#222"/></svg></span><span class="bar"><i></i></span><span class="time">00:00</span></div></article>

  <article class="sermon-card" style="left:195px;top:2312px"><div class="avatar" role="img" aria-label="Speaker portrait"></div><div class="by">Spoken By Ruth K.</div><h3>Printer took a galley of type and scrambled it to</h3><span class="tag">Sermon 1</span><div class="player"><span class="play"><svg width="7" height="8" viewBox="0 0 7 8"><path d="M0 0l7 4-7 4z" fill="#222"/></svg></span><span class="bar"><i></i></span><span class="time">00:00</span></div></article>
  <article class="sermon-card" style="left:400px;top:2312px"><div class="avatar" role="img" aria-label="Speaker portrait"></div><div class="by">Spoken By Ruth K.</div><h3>Printer took a galley of type and scrambled it to</h3><span class="tag">Sermon 2</span><div class="player"><span class="play"><svg width="7" height="8" viewBox="0 0 7 8"><path d="M0 0l7 4-7 4z" fill="#222"/></svg></span><span class="bar"><i></i></span><span class="time">00:00</span></div></article>
  <article class="sermon-card" style="left:607px;top:2312px"><div class="avatar" role="img" aria-label="Speaker portrait"></div><div class="by">Spoken By Ruth K.</div><h3>Printer took a galley of type and scrambled it to</h3><span class="tag">Sermon 3</span><div class="player"><span class="play"><svg width="7" height="8" viewBox="0 0 7 8"><path d="M0 0l7 4-7 4z" fill="#222"/></svg></span><span class="bar"><i></i></span><span class="time">00:00</span></div></article>
  <article class="sermon-card" style="left:814px;top:2312px"><div class="avatar" role="img" aria-label="Speaker portrait"></div><div class="by">Spoken By Ruth K.</div><h3>Printer took a galley of type and scrambled it to</h3><span class="tag">Sermon 4</span><div class="player"><span class="play"><svg width="7" height="8" viewBox="0 0 7 8"><path d="M0 0l7 4-7 4z" fill="#222"/></svg></span><span class="bar"><i></i></span><span class="time">00:00</span></div></article>

  <a class="btn" style="left:529px;top:2597px;width:142px;height:40px">Explorer More <svg viewBox="0 0 8 12"><path d="M1 1l5 5-5 5" fill="none" stroke="#fff" stroke-width="1.5"/></svg></a>
</section>

<!-- Articles of Faith -->
<section>
  <div class="abs articles"></div>
  <h2 class="section-title" style="top:2758px">Articles of Faith</h2>

  <article class="article" style="left:195px"><div class="pic" role="img" aria-label="Photograph of the church building" style="background:linear-gradient(180deg,#d8d8d8 0%,#cfcfcf 40%,#8c715d 55%,#b3a89c 75%,#cfc7bd 100%)"></div><div class="kicker">EVENTS</div><h3>The God Head</h3><p>We believe in the God head bodily, known as the Divine Trinity. This body consist of God the Father, Jesus Christ, his only begotten son and the.</p><div class="more">Know More <svg width="6" height="9" viewBox="0 0 6 9"><path d="M1 1l3.5 3.5L1 8" fill="none" stroke="#222" stroke-width="1.4"/></svg></div></article>
  <article class="article" style="left:470px"><div class="pic" role="img" aria-label="Photograph of a cathedral interior with wooden pews" style="background:linear-gradient(180deg,#8fa9c2 0%,#b8a38a 45%,#8a6a48 75%,#5d4a3a 100%)"></div><div class="kicker">EVENTS</div><h3>Full Salvation.</h3><p>We believe that Salvation is received only when a person comes to the realization that he or she is lost and separated from God and becomes full of godly sorrow.</p><div class="more">Know More <svg width="6" height="9" viewBox="0 0 6 9"><path d="M1 1l3.5 3.5L1 8" fill="none" stroke="#222" stroke-width="1.4"/></svg></div></article>
  <article class="article" style="left:745px"><div class="pic" role="img" aria-label="Photograph of a white chapel interior with rows of pews" style="background:linear-gradient(180deg,#e6ecef 0%,#cfd6da 45%,#9a5a4a 75%,#7a4a3c 100%)"></div><div class="kicker">EVENTS</div><h3>Sanctification.</h3><p>We believe sanctification is the work of grace that sets the believer apart for God, a cleansing that grows through faith and the Word.</p><div class="more">Know More <svg width="6" height="9" viewBox="0 0 6 9"><path d="M1 1l3.5 3.5L1 8" fill="none" stroke="#222" stroke-width="1.4"/></svg></div></article>
</section>

<!-- Support -->
<section class="abs support">
  <h2>Support Our Church</h2>
  <p>Christian Refugees in crisis. We are raising funds for these survivors who are facing cold winter weather without shelter, clothes, blankets, food &amp; water. People are sleeping outside anywhere they can find a somewhat safe spot. Helping your supporters overcome challenges to consistently give can be tough.</p>
  <a class="btn" style="left:536px;top:217px;width:128px;height:38px">Donate Now <svg viewBox="0 0 8 12"><path d="M1 1l5 5-5 5" fill="none" stroke="#fff" stroke-width="1.5"/></svg></a>
</section>

<!-- Announcements -->
<section>
  <h2 class="light-title" style="top:3718px">Important Announcement</h2>
  <div class="abs notice-left">
    <h3>Chruch<br>Closed</h3>
    <div class="when">Monday - Friday<br>20 feb to 25 feb</div>
  </div>
  <div class="abs notice-art" role="img" aria-label="Illustration of a megaphone with an important announcement ribbon"></div>
  <div class="abs notice-right">
    <div class="brand"><span class="mark"></span>GRACE HILL</div>
    <div class="head">"Service time Change</div>
    <div class="art" role="img" aria-label="Illustration of a megaphone with a service time announcement banner"></div>
  </div>
</section>

<!-- Contact -->
<section>
  <h2 class="light-title" style="top:4098px">Let's Talk With Us</h2>
  <form class="abs contact">
    <div class="field" style="left:52px;top:42px">First Name<div class="line">|</div></div>
    <div class="field" style="left:288px;top:42px">Last Name<div class="line"><svg width="9" height="10" viewBox="0 0 9 10"><circle cx="4.5" cy="3" r="2.5" fill="#fff"/><path d="M0 10a4.5 4 0 0 1 9 0z" fill="#fff"/></svg>Smith</div></div>
    <div class="field" style="left:52px;top:124px">Contact Number<div class="line"><svg width="9" height="9" viewBox="0 0 9 9"><path d="M1 1l2 0 1 2-1 1a5 5 0 0 0 2 2l1-1 2 1v2a7 7 0 0 1-7-7z" fill="#fff"/></svg>+1-555-010-0199</div></div>
    <div class="field" style="left:288px;top:124px">Email Address<div class="line"><svg width="10" height="8" viewBox="0 0 10 8"><rect x=".5" y=".5" width="9" height="7" fill="none" stroke="#fff"/><path d="M.5 .5l4.5 4 4.5-4" fill="none" stroke="#fff"/></svg>name@mailbox.com</div></div>
    <div class="field" style="left:52px;top:206px;width:436px">Message<div class="line" style="height:20px"><svg width="9" height="9" viewBox="0 0 9 9"><path d="M1 8l1-3 5-5 2 2-5 5z" fill="#fff"/></svg>Hello...</div><div style="border-bottom:1px solid rgba(255,255,255,.75);height:38px"></div></div>
    <a class="btn" style="left:197px;top:311px;width:146px;height:40px">Submit Details <svg viewBox="0 0 8 12"><path d="M1 1l5 5-5 5" fill="none" stroke="#fff" stroke-width="1.5"/></svg></a>
  </form>
</section>

<!-- Footer -->
<footer class="abs footer">
  <div class="brand" style="position:absolute;left:526px;top:78px"><span class="mark"></span>GRACE HILL</div>
  <nav class="footer-nav"><span>Home</span><span>About</span><span>Pastor</span><span>Listen Live</span><span>Library</span><span>Donation</span><span>Support Us</span><span>Member Login</span></nav>
  <div class="addr">218 Maple Ridge Lane, Harlow, Ohio 44021</div>
  <div class="socials"><span></span><span></span><span></span><span></span></div>
  <div class="copy">© Copyright Grace Hill Church 2023. All Right Reserved.</div>
</footer>

</body>
</html>
```